Website art for a private investigator.

The purposed graphic is for a business website ( brellwick.com ). The business name is “Harrowgate & Associates ltd.” This firm is a private investigation agency. The purposed graphic will be placed in the upper most main area of the main page of the website. If you look at the website now there is no graphic.

I have an idea of what I am looking for. I imagine a graphic depicting a contemporary private investigator walking through a dark alley searching for some unknown item. This is symbolic of private investigators hired to find information for people who their selfs do not have the know how nor could they handle the complexity and high stress environment. When I say contemporary I am referring to todays private investigators typically highly educated and well dressed.

Target Market(s)

People who need a private investigator

Industry/Entity Type

Business

Requirements
Must have
• match website; I have an idea of what I am looking for. I imagine a graphic depicting a contemporary private investigator walking through a dark alley searching for some unknown item. This is symbolic of private investigators hired to find information for people who their selfs do not have the know how nor could they handle the complexity and high stress environment. When I say contemporary I am referring to todays private investigators typically highly educated and well dressed.
Should not have
• Everyone please understand, I am not looking for a new website. I am only looking for the image. If you have submitted a design and its displayed on another website other than mine. I will not select your design. I am sorry for being harsh, but I asked for the image to match my website.

```html
<!DOCTYPE html>
<html lang="en">
<head>
<meta charset="utf-8">
<title>Harrowgate &amp; Associates ltd. — Private Investigation</title>
<link rel="stylesheet" href="https://fonts.googleapis.com/css2?family=Montserrat:wght@400;500;600;700&family=Lato:ital,wght@0,400;0,700;1,400;1,700&display=swap">
<style>
  :root {
    --page-bg: #ffffff;
    --night-deep: #07090c;
    --night-mid: #2a3845;
    --night-light: #4a5f72;
    --night-glow: rgba(150, 175, 196, 0.55);
    --social-bar: #0a0a0a;
    --social-icon: #e6e6e6;
    --nav-text: #ffffff;
    --nav-muted: #aab6c1;
    --ink: #1f1f1f;
    --ink-soft: #444444;
    --quote-mark: #c9c9c9;
    --button-top: #1f93f2;
    --button-bottom: #0862c6;
    --button-edge: #0650a3;
  }
  * { box-sizing: border-box; margin: 0; padding: 0; }
  html, body {
    width: 1200px; height: 900px; overflow: hidden;
    background: var(--page-bg);
  }
  .canvas { position: relative; width: 1200px; height: 900px; }

  /* Banner */
  .hero {
    position: absolute; left: 50px; top: 56px; width: 1100px; height: 158px;
    overflow: hidden;
  }
  .hero-scene {
    position: absolute; inset: 0;
    background:
      radial-gradient(ellipse 130px 150px at 600px 10px, var(--night-glow), transparent 72%),
      radial-gradient(ellipse 70px 60px at 1068px 48px, rgba(140, 165, 188, 0.35), transparent 70%),
      radial-gradient(ellipse 380px 70px at 330px 150px, rgba(95, 118, 138, 0.45), transparent 75%),
      linear-gradient(180deg, rgba(0,0,0,0) 55%, rgba(0,0,0,0.35) 100%),
      linear-gradient(90deg,
        #151d25 0%, var(--night-mid) 18%, #364858 34%,
        var(--night-light) 48%, #34434f 56%,
        #141a21 66%, #0c1015 80%, var(--night-deep) 100%);
  }

  .social-bar {
    position: absolute; left: 0; top: 0; width: 229px; height: 34px;
    background: var(--social-bar);
    display: flex; align-items: center; gap: 24px; padding-left: 22px;
  }
  .social-icon {
    width: 10px; height: 10px; border-radius: 50%;
    background: var(--social-icon);
  }

  .main-nav {
    position: absolute; left: 252px; top: 13px;
    font-family: "Lato", sans-serif; font-weight: 700; font-size: 7px;
    color: var(--nav-text);
  }
  .main-nav span { position: absolute; white-space: nowrap; }
  .main-nav .is-current { color: var(--nav-muted); font-weight: 400; }

  .hero-title {
    position: absolute; left: 273px;
    font-family: "Montserrat", sans-serif; font-weight: 700;
    color: #ffffff; font-size: 12px; white-space: nowrap;
  }
  .hero-title.firm { top: 58px; }
  .hero-title.tagline { top: 91px; }

  /* Contact */
  .contact-phone {
    position: absolute; left: 669px; top: 232px;
    font-family: "Montserrat", sans-serif; font-weight: 500;
    font-size: 12px; color: var(--ink);
  }
  .request-button {
    position: absolute; left: 672px; top: 258px; width: 117px; height: 20px;
    border-radius: 10px; border: 1px solid var(--button-edge);
    background: linear-gradient(var(--button-top), var(--button-bottom));
    color: #fff; font-family: "Lato", sans-serif; font-weight: 700; font-size: 7.5px;
    display: flex; align-items: center; justify-content: center;
  }

  /* Content */
  .section-heading {
    position: absolute; left: 323px; top: 315px;
    font-family: "Montserrat", sans-serif; font-size: 15px;
    color: var(--ink); font-weight: 500;
  }
  .quote-mark {
    position: absolute; font-family: "Lato", serif; font-style: italic; font-weight: 700;
    font-size: 36px; line-height: 1; color: var(--quote-mark);
  }
  .quote-text {
    position: absolute; left: 327px;
    font-family: "Lato", sans-serif; font-style: italic;
    font-size: 9px; line-height: 15px; color: var(--ink);
  }
  .quote-text.mission { top: 369px; width: 525px; font-weight: 700; }
  .quote-text.testimonial { top: 473px; width: 545px; font-weight: 400; }
  .quote-attribution {
    position: absolute; right: 327px; top: 506px;
    font-family: "Lato", sans-serif; font-size: 5.6px; color: var(--ink-soft);
    white-space: nowrap;
  }
</style>
</head>
<body>
<div class="canvas">
  <header class="hero">
    <div class="hero-scene" role="img" aria-label="Moody night alley lit by streetlamps, a well dressed investigator in hat and long coat searching the shadows"></div>

    <div class="social-bar" aria-label="Social links">
      <span class="social-icon"></span><span class="social-icon"></span><span class="social-icon"></span>
      <span class="social-icon"></span><span class="social-icon"></span><span class="social-icon"></span>
    </div>

    <nav class="main-nav">
      <span class="is-current" style="left:0">Main</span>
      <span style="left:40px">Investigation &amp; Analysis</span>
      <span style="left:139px">News</span>
      <span style="left:179px">Fees</span>
    </nav>

    <h1 class="hero-title firm">Harrowgate &amp; Associates ltd.</h1>
    <p class="hero-title tagline">A Private Investigation and Analysis Firm</p>
  </header>

  <p class="contact-phone">Tel. (555) 214-7360</p>
  <div class="request-button">Sudmit Request For Service</div>

  <h2 class="section-heading">Ohio and West Virginia Private Investigators</h2>

  <span class="quote-mark" style="left:325px;top:348px;">“</span>
  <p class="quote-text mission">Our experience and unbiased approach is your greatest strength! If you are an attorney, company, or private individual with a legal need we will provide you with accurate, timely and unbiassed information that will help you make an informed decision, mitigate risk, and resolve problems.</p>
  <span class="quote-mark" style="left:827px;top:414px;">”</span>

  <span class="quote-mark" style="left:325px;top:452px;">“</span>
  <p class="quote-text testimonial">Harrowgate &amp; Associates, Ltd. have been very helpful in our requests. Daniel is a very courteous and respectful person. Thanks for all you have done thus far!!! We will definitely use this firm in the future!!</p>
  <p class="quote-attribution">— Calvin R. Ashby, Jr., Attorney at Law, Ashby Law Office - South Point, Ohio</p>
  <span class="quote-mark" style="left:856px;top:517px;">”</span>
</div>
</body>
</html>
```